Staff Newsletter Template Image

We are looking for two .jpg images that we can put into a Word document and use for our staff newsletter. We will then add content using text boxes.
Attached is the current template which works for the columns and size that we need but we just want a fresh new design.
The Word document shows how we use it.
The name will stay the same - Brightwave Post but can be a different look to the current one.

Target Market(s)

Sales team

Colors

Designer to choose colors to be used in the design.

Requirements
Must have
• Colours will be green, grey and white, possibly cream if needed. All from the guidelines.
• I have attached our brand guidelines which shows design elements and fonts for our brand. Also attached is brand guidelines for one of our product lines as we would like to use the same green.
• It needs to be nice to look at and motivational for our team

```html
<!DOCTYPE html>
<html lang="en">
<head>
<meta charset="utf-8">
<title>Brightwave Post – Staff Newsletter</title>
<link rel="stylesheet" href="https://fonts.googleapis.com/css2?family=Jost:ital,wght@0,300;0,400;0,500;0,600;1,300;1,400&family=Lato:wght@400&display=swap">
<style>
  :root {
    --backdrop: #e5c8ae;
    --green: #7dbf35;
    --charcoal: #2b2b2e;
    --charcoal-deep: #202022;
    --ink: #222224;
    --body: #4a4a4d;
    --white: #ffffff;
    --tan: #d99a6c;
    --rule: #dcdcdc;
  }
  * { box-sizing: border-box; margin: 0; padding: 0; }
  html, body { width: 1200px; height: 915px; overflow: hidden; background: var(--backdrop); }
  .canvas { position: relative; width: 1200px; height: 915px; font-family: "Jost", sans-serif; }
  .shapes { position: absolute; inset: 0; width: 1200px; height: 915px; }
  .block { position: absolute; }
  .heading { font-weight: 500; font-size: 13px; letter-spacing: 0.6px; text-transform: uppercase; line-height: 14.7px; }
  .heading.dark { color: var(--ink); }
  .heading.light { color: var(--white); }
  .body-copy { font-weight: 300; font-size: 9.4px; line-height: 14.7px; color: var(--body); }
  .body-copy p + p { margin-top: 5.8px; }

  .masthead { left: 71px; top: 82px; font-weight: 500; font-size: 38px; color: var(--ink); letter-spacing: 0.5px; line-height: 48px; }

  .sellers-intro { left: 338px; top: 253px; width: 212px; font-weight: 300; font-size: 9.3px; line-height: 14.7px; color: #cfcfd2; }
  .sellers-intro strong { color: var(--green); font-weight: 600; }
  .team-label { left: 338px; top: 294px; font-weight: 500; font-size: 10px; color: var(--white); }
  .rank-list { left: 338px; top: 316px; list-style: none; font-size: 8.8px; line-height: 14.7px; font-weight: 600; }
  .rank-list li { color: var(--green); }
  .rank-list .rank { display: inline-block; width: 14px; color: var(--white); }

  .tick-list { list-style: none; font-style: italic; font-weight: 300; font-size: 8.7px; color: var(--white); }
  .tick-list li { display: flex; align-items: center; height: 18.3px; }
  .tick-list svg { width: 8px; height: 8px; margin-right: 6px; flex: none; }

  .shout-name { left: 348px; top: 569px; font-size: 10.5px; color: var(--tan); font-weight: 400; }
  .shout-copy { left: 348px; top: 588px; width: 200px; font-style: italic; font-weight: 300; font-size: 8.7px; line-height: 15.8px; color: var(--white); }

  .news-item { left: 635px; width: 230px; }
  .news-date { font-size: 10px; color: var(--green); font-weight: 400; line-height: 14px; }
  .news-title { font-size: 8.6px; font-weight: 600; color: var(--ink); line-height: 17px; }
  .news-text { font-size: 8.6px; font-weight: 300; color: var(--body); line-height: 13.6px; }

  .reminders { left: 635px; top: 428px; width: 230px; }
  .reminders p { font-size: 8.6px; font-weight: 300; color: var(--body); line-height: 13.6px; height: 35.1px; }

  .member-copy { left: 901px; top: 512px; width: 205px; font-style: italic; font-weight: 300; font-size: 8.7px; line-height: 14.7px; color: var(--white); }

  .footer-note { font-family: "Lato", sans-serif; font-size: 6.4px; color: #b9b9bc; position: absolute; transform: translateX(-50%); }
  .page-count { font-family: "Lato", sans-serif; font-size: 6.2px; color: #a9a9ac; position: absolute; }
</style>
</head>
<body>
<svg width="0" height="0" style="position:absolute" aria-hidden="true">
  <symbol id="tick" viewBox="0 0 16 16">
    <circle cx="8" cy="8" r="8" fill="#7dbf35"/>
    <path d="M4.5 8.3 7 10.7 11.6 5.6" fill="none" stroke="#202022" stroke-width="2" stroke-linecap="round" stroke-linejoin="round"/>
  </symbol>
</svg>

<main class="canvas">
  <svg class="shapes" viewBox="0 0 2203 1680" preserveAspectRatio="none" aria-hidden="true">
    <!-- front page -->
    <rect x="102" y="79" width="950" height="1466" fill="#ffffff"/>
    <polygon points="102,291 283,291 102,370" fill="#7dbf35"/>
    <polygon points="310,291 612,291 420,376 122,376" fill="#7dbf35"/>
    <polygon points="1052,112 1052,376 455,376" fill="#7dbf35"/>
    <rect x="578" y="376" width="474" height="1169" fill="#2b2b2e"/>
    <polygon points="102,1298 578,1188 578,1545 102,1545" fill="#7dbf35"/>
    <line x1="130" y1="1462" x2="546" y2="1462" stroke="#a9d67a" stroke-width="1.5"/>
    <rect x="620" y="689" width="384" height="282" rx="12" fill="#202022"/>
    <rect x="620" y="987" width="384" height="200" rx="12" fill="#202022"/>
    <rect x="102" y="1545" width="950" height="55" fill="#2a2a2d"/>
    <!-- back page -->
    <rect x="1137" y="79" width="475" height="1061" fill="#ffffff"/>
    <rect x="1612" y="79" width="474" height="1061" fill="#2b2b2e"/>
    <polygon points="1612,843 2086,733 2086,1140 1612,1140" fill="#7dbf35"/>
    <line x1="1165" y1="709" x2="1580" y2="709" stroke="#dcdcdc" stroke-width="1.5"/>
    <rect x="1137" y="1140" width="949" height="57" fill="#2a2a2d"/>
  </svg>

  <!-- front page content -->
  <div class="block masthead">Brightwave Post</div>

  <h2 class="block heading dark" style="left:71px; top:229px;">Hi everyone,</h2>
  <div class="block body-copy" style="left:71px; top:251px; width:230px;">
    <p>Lorem ipsum dolor sit amet, consectetur adipiscing elit. Donec aliquet orci odio, eu convallis dui imperdiet id. Praesent ultrices ligula et nulla pharetra tristique. Quisque dolor est, auctor vel scelerisque sed, cursus at velit. Donec cursus feugiat dui vitae pellentesque. Phasellus semper, elit sed placerat rhoncus, tortor sem posuere lacus, tincidunt dictum augue leo a mauris. Cras lacinia nunc ante, a efficitur urna euismod efficitur</p>
    <p>Quisque dolor est, auctor vel scelerisque sed, cursus at velit. Donec cursus feugiat dui vitae pellentesque. Phasellus semper, elit sed placerat rhoncus, tortor sem posuere lacus, tincidunt dictum augue leo a mauris. Cras lacinia nunc ante, a efficitur urna euismod efficitur</p>
  </div>

  <h2 class="block heading light" style="left:338px; top:229px;">Top sellers!</h2>
  <p class="block sellers-intro">The following Brightwave team members were our top sellers last week <strong>based on completed sales</strong></p>
  <div class="block team-label">Team Member</div>
  <ol class="block rank-list">
    <li><span class="rank">1.</span>100 Brightwave Dollars</li>
    <li><span class="rank">2.</span>50 Brightwave Dollars</li>
    <li><span class="rank">3.</span>25 Brightwave Dollars</li>
  </ol>

  <h2 class="block heading light" style="left:348px; top:387px;">Top tip from our week’s<br>top seller</h2>
  <ul class="block tick-list" style="left:348px; top:427px;">
    <li><svg><use href="#tick"/></svg>Quisque id enim sapien.</li>
    <li><svg><use href="#tick"/></svg>Phasellus vulputate dignissim tincidunt.</li>
    <li><svg><use href="#tick"/></svg>Duis mattis eleifend leo ac tempus.</li>
    <li><svg><use href="#tick"/></svg>Duis vel diam convallis.</li>
    <li><svg><use href="#tick"/></svg>Phasellus vulputate dignissim tincidunt.</li>
  </ul>

  <h2 class="block heading light" style="left:348px; top:550px;">Shout out</h2>
  <div class="block shout-name">Name</div>
  <p class="block shout-copy">Phasellus vulputate dignissim tincidunuis mattis eleifend leo ac tempu vel diam convallis vulputate dignissim tincidunt.</p>

  <div class="footer-note" style="left:314px; top:854px;">Copyright © CompanyName All rights reserved</div>
  <div class="page-count" style="left:557px; top:855px;">x10</div>

  <!-- back page content -->
  <h2 class="block heading dark" style="left:635px; top:71px;">Company news</h2>
  <article class="block news-item" style="top:101px;">
    <div class="news-date">December 4, 2019</div>
    <div class="news-title">Quisque dolor est, auctor vel scelerisque sed.</div>
    <p class="news-text">Donec cursus feugiat dui vitae pellentesque elit sed placerat rhoncus, tortor sem posuere lacus tincidunt.</p>
  </article>
  <article class="block news-item" style="top:172px;">
    <div class="news-date">December 4, 2019</div>
    <div class="news-title">Quisque dolor est, auctor vel scelerisque sed.</div>
    <p class="news-text">Donec cursus feugiat dui vitae pellentesque elit sed placerat rhoncus, tortor sem posuere lacus tincidunt.</p>
  </article>
  <article class="block news-item" style="top:243px;">
    <div class="news-date">December 4, 2019</div>
    <div class="news-title">Quisque dolor est, auctor vel scelerisque sed.</div>
    <p class="news-text">Donec cursus feugiat dui vitae pellentesque elit sed placerat rhoncus, tortor sem posuere lacus tincidunt.</p>
  </article>
  <article class="block news-item" style="top:313px;">
    <div class="news-date">December 4, 2019</div>
    <div class="news-title">Quisque dolor est, auctor vel scelerisque sed.</div>
    <p class="news-text">Donec cursus feugiat dui vitae pellentesque elit sed placerat rhoncus, tortor sem posuere lacus tincidunt.</p>
  </article>

  <h2 class="block heading dark" style="left:635px; top:406px;">Reminders</h2>
  <div class="block reminders">
    <p>Donec cursus feugiat dui vitae pellentesque elit sed placerat rhoncus, tortor sem posuere lacus tincidunt.</p>
    <p>Donec cursus feugiat dui vitae pellentesque elit sed placerat rhoncus, tortor sem posuere lacus tincidunt.</p>
    <p>Donec cursus feugiat dui vitae pellentesque elit sed placerat rhoncus, tortor sem posuere lacus tincidunt.</p>
    <p>Donec cursus feugiat dui vitae pellentesque elit sed placerat rhoncus, tortor sem posuere lacus tincidunt.</p>
    <p>Donec cursus feugiat dui vitae pellentesque elit sed placerat rhoncus, tortor sem posuere lacus tincidunt.</p>
  </div>

  <h2 class="block heading light" style="left:911px; top:71px;">Tips &amp; hints</h2>
  <ul class="block tick-list" style="left:911px; top:90px;">
    <li><svg><use href="#tick"/></svg>Quisque id enim sapien.</li>
    <li><svg><use href="#tick"/></svg>Phasellus vulputate dignissim tincidunt.</li>
    <li><svg><use href="#tick"/></svg>Duis mattis eleifend leo ac tempus.</li>
    <li><svg><use href="#tick"/></svg>Duis vel diam convallis.</li>
    <li><svg><use href="#tick"/></svg>Phasellus vulputate dignissim tincidunt.</li>
    <li><svg><use href="#tick"/></svg>Nullam odio sapien, pharetra blandit auctor.</li>
  </ul>

  <h2 class="block heading light" style="left:901px; top:475px;">Being a Brightwave team<br>member means...</h2>
  <p class="block member-copy">Quisque dolor est, auctor vel scelerisque sed, cursus at velit. Donec cursus feugiat dui vitae pellentesque. Phasellus semper, elit sed placerat rhoncus, tortor sem posuere lacus, tincidunt dictum augue leo a mauris. Cras lacinia nunc ante, a efficitur urna euismod efficitur.</p>

  <div class="footer-note" style="left:878px; top:634px;">Copyright © CompanyName All rights reserved</div>
  <div class="page-count" style="left:1120px; top:636px;">x10</div>
</main>
</body>
</html>
```